Oil and Gas Exploration and Production company needs a business card design

We need a business card design using our logo and colors in the logo. We want a mainstream design.

```html
<!DOCTYPE html>
<html lang="en">
<head>
<meta charset="utf-8">
<title>Sunvale Oil &amp; Gas — Business Card</title>
<link rel="stylesheet" href="https://fonts.googleapis.com/css2?family=EB+Garamond:wght@400;700;800&display=swap">
<style>
  :root {
    --page-bg: #e4e4e4;
    --card-bg: #f6f6f6;
    --gold: #cf9b32;
    --ink: #1a1a1a;
    --text: #2b2b2b;
  }
  * { margin: 0; padding: 0; box-sizing: border-box; }
  html, body {
    width: 1200px;
    height: 586px;
    overflow: hidden;
    background: var(--page-bg);
  }
  .business-card {
    position: absolute;
    left: 150px;
    top: 23px;
    width: 900px;
    height: 540px;
    background: var(--card-bg);
    font-family: "EB Garamond", Georgia, serif;
    color: var(--text);
    overflow: hidden;
  }
  .side-band {
    position: absolute;
    top: 50px;
    width: 32px;
    height: 395px;
    background: var(--gold);
  }
  .side-band--left { left: 0; border-radius: 0 32px 32px 0; }
  .side-band--right { right: 0; border-radius: 32px 0 0 32px; }

  .brand {
    position: absolute;
    top: 92px;
    left: 0;
    width: 100%;
    display: flex;
    justify-content: center;
    align-items: center;
    gap: 18px;
  }
  .brand-dot {
    width: 54px;
    height: 54px;
    border-radius: 50%;
    background: var(--gold);
  }
  .brand-name {
    font-weight: 800;
    font-size: 66px;
    line-height: 1;
    color: var(--ink);
    letter-spacing: -0.5px;
  }

  .contact-list {
    position: absolute;
    left: 72px;
    top: 333px;
    list-style: none;
  }
  .contact-item {
    display: flex;
    align-items: center;
    height: 36.5px;
    font-size: 19px;
  }
  .contact-icon {
    width: 18px;
    height: 18px;
    margin-right: 16px;
    fill: var(--gold);
    flex-shrink: 0;
  }

  .person {
    position: absolute;
    right: 72px;
    top: 347px;
    text-align: right;
  }
  .person-name {
    font-weight: 700;
    font-size: 21px;
    color: var(--gold);
    line-height: 1.2;
  }
  .person-title {
    font-size: 18px;
    line-height: 1.4;
  }
  .address {
    position: absolute;
    right: 72px;
    top: 435px;
    font-weight: 700;
    font-size: 19px;
    color: var(--gold);
  }
</style>
</head>
<body>
  <section class="business-card">
    <div class="side-band side-band--left"></div>
    <div class="side-band side-band--right"></div>

    <header class="brand">
      <span class="brand-dot"></span>
      <span class="brand-name">Sunvale Oil &amp; Gas</span>
    </header>

    <ul class="contact-list">
      <li class="contact-item">
        <svg class="contact-icon" viewBox="0 0 20 20" aria-hidden="true">
          <path d="M2 7c0-3 4-4 8-4s8 1 8 4v1.5h-4V7H6v1.5H2z"/>
          <path d="M5 10h10l2 7H3z M10 11.5a2.5 2.5 0 1 0 0 5a2.5 2.5 0 1 0 0-5z" fill-rule="evenodd"/>
        </svg>
        <span>555.210.4471</span>
      </li>
      <li class="contact-item">
        <svg class="contact-icon" viewBox="0 0 20 20" aria-hidden="true">
          <path d="M4 2l3 0 2 5-2 1.5c1 2.2 2.8 4 5 5L13.5 11l5 2v3c0 1-1 2-2 2C9 18 2 11 2 4c0-1 1-2 2-2z"/>
        </svg>
        <span>555.318.2096</span>
      </li>
      <li class="contact-item">
        <svg class="contact-icon" viewBox="0 0 20 20" aria-hidden="true">
          <path d="M5 2h10v5H5z"/>
          <path d="M2 8h16v7h-3v-3H5v3H2z"/>
          <path d="M6 13h8v5H6z"/>
        </svg>
        <span>555.427.6610</span>
      </li>
      <li class="contact-item">
        <svg class="contact-icon" viewBox="0 0 20 20" aria-hidden="true">
          <path d="M2 5h16v1l-8 5-8-5z"/>
          <path d="M2 7.5l8 5 8-5V16H2z"/>
        </svg>
        <span>dwhitfield@sunvaleenergy.com</span>
      </li>
    </ul>

    <div class="person">
      <p class="person-name">Dana Whitfield</p>
      <p class="person-title">Chief Executive Offer</p>
    </div>

    <p class="address">4150 Ridge Park Dr, Suite 210, Cary, NC 27513</p>
  </section>
</body>
</html>
```